Business Card for a Jewellery Brand

Business card for an upscale jewellery brand. Attached is the brand logo and icon and color board. I am looking for two card versions: one for the founder and one is generic. The card should be elegant and convey upscale and premium feel. I am open to both square and rectangle card shapes.

Industry/Entity Type

Jewelry

Contact Information for Business Card

Two cards: (1) Sunela Parvaniya (Founder) (2) General
(1) Sunela Parvaniya card should have Name: Sunela Parvaniya, Title: Founder Email id: sunela@quiremo.com.au. Phone no: +61452913307
(2) Generic card should have Email id: info@quiremo.com.au. Phone no: +61436207518

Requirements
Must have
• Workmark
• ICON
• Phone no
• Email ID
• ABN: 58219740312 (Note: ABN is Business number in Australia)
• Website: www.quiremo.com.au
• Instagram: quiremo_jewellery
• Facebook: @quiremojewellery
Nice to have
• Tagline

```html
<!DOCTYPE html>
<html lang="en">
<head>
<meta charset="utf-8">
<title>Quiremo Business Card – Founder</title>
<link rel="stylesheet" href="https://fonts.googleapis.com/css2?family=Play:wght@400;700&family=Saira+Condensed:wght@700&display=swap">
<style>
  :root {
    --backdrop: #5b5b5b;
    --card: #0d0d0e;
    --rose: #e3918c;
    --ink: #ecebea;
  }
  * { margin: 0; padding: 0; box-sizing: border-box; }
  html, body {
    width: 1200px; height: 867px; overflow: hidden;
    background: var(--backdrop);
  }
  .canvas {
    position: relative; width: 1200px; height: 867px;
    display: flex; align-items: center; justify-content: center;
  }
  .card {
    width: 880px; height: 500px;
    background: var(--card);
    border-radius: 4px;
    box-shadow: 0 18px 40px rgba(0,0,0,.35);
    display: flex; flex-direction: column; align-items: center;
    padding-top: 92px;
    font-family: "Play", sans-serif;
    color: var(--ink);
  }
  .wordmark {
    font-family: "Play", sans-serif;
    font-weight: 400;
    font-size: 50px;
    letter-spacing: 18px;
    margin-right: -18px;
    color: var(--rose);
    line-height: 1;
  }
  .person-name {
    margin-top: 26px;
    font-family: "Saira Condensed", sans-serif;
    font-weight: 700;
    font-size: 38px;
    letter-spacing: 2px;
    text-transform: uppercase;
    color: var(--rose);
    line-height: 1;
  }
  .person-title {
    margin-top: 6px;
    font-size: 22px;
    line-height: 1.2;
  }
  .contact-list {
    margin-top: 18px;
    display: flex; flex-direction: column; align-items: center; gap: 6px;
    font-size: 21px;
  }
  .contact-row { display: flex; align-items: center; gap: 16px; }
  .contact-item { display: flex; align-items: center; gap: 7px; }
  .contact-icon { width: 18px; height: 18px; flex: none; }
  .contact-icon * { fill: none; stroke: var(--rose); stroke-width: 1.8; }
  .contact-icon .solid { fill: var(--rose); stroke: none; }
</style>
</head>
<body>
<main class="canvas">
  <article class="card">
    <div class="wordmark">QUIREMO</div>
    <h1 class="person-name">Sunela Parvaniya</h1>
    <p class="person-title">Founder</p>

    <div class="contact-list">
      <div class="contact-row">
        <span class="contact-item">
          <svg class="contact-icon" viewBox="0 0 18 18" aria-hidden="true"><rect x="4.5" y="1.5" width="9" height="15" rx="1.5"/><line x1="7.5" y1="13.5" x2="10.5" y2="13.5"/></svg>
          +61452913307
        </span>
        <span class="contact-item">
          <svg class="contact-icon" viewBox="0 0 18 18" aria-hidden="true"><rect x="1.5" y="4" width="15" height="10" rx="1"/><polyline points="1.5,4.5 9,10 16.5,4.5"/></svg>
          sunela@quiremo.com.au
        </span>
      </div>
      <div class="contact-row">
        <span class="contact-item">
          <svg class="contact-icon" viewBox="0 0 18 18" aria-hidden="true"><circle cx="9" cy="9" r="7.5"/><ellipse cx="9" cy="9" rx="3.2" ry="7.5"/><line x1="1.5" y1="9" x2="16.5" y2="9"/></svg>
          quiremo.com.au
        </span>
        <span class="contact-item">
          <svg class="contact-icon" viewBox="0 0 18 18" aria-hidden="true"><rect class="solid" x="2" y="2" width="14" height="14" rx="2"/></svg>
          quiremo_jewellery
        </span>
        <span class="contact-item">
          <svg class="contact-icon" viewBox="0 0 18 18" aria-hidden="true"><circle class="solid" cx="9" cy="9" r="7.5"/></svg>
          @quiremojewellery
        </span>
      </div>
      <div class="contact-row">
        <span class="contact-item">ABN:58219740312</span>
      </div>
    </div>
  </article>
</main>
</body>
</html>
```